Harborline Freight online presence/customer portal track shipping

I sleek design showing what we do, broker freight. What we specialize in, chemicals and any freight where domestic or international. We want a home page, a customer portal button on front page that lets clients check on status of their freight (integrate with our transportation management system. Contact page,
COMPANIES THAT HAVE PALLETS TO MOVE.
https://www.tallowmerelogistics.com/
https://www.quivendale.com/
https://www.rkpellow.com/
3 page

```html
<!DOCTYPE html>
<html lang="en">
<head>
<meta charset="utf-8">
<title>Caldera Logistics — Freight Brokerage</title>
<link rel="stylesheet" href="https://fonts.googleapis.com/css2?family=Poppins:wght@400;500;600;700;800&family=Open+Sans:wght@400;600&display=swap">
<style>
:root{
  --navy:#1f3f8e;
  --blue:#2b5ea7;
  --red:#e8343f;
  --teal:#2eb096;
  --paper:#f5f2f2;
  --ink:#1d1d1d;
  --muted:#4a4a4a;
  --footer:#232323;
  --white:#ffffff;
}
*{margin:0;padding:0;box-sizing:border-box}
html,body{width:1200px;height:4471px;overflow:hidden}
body{position:relative;font-family:"Open Sans",sans-serif;color:var(--ink);background:var(--paper)}
.abs{position:absolute}
h1,h2,h3,h4,.btn,.nav a{font-family:"Poppins",sans-serif}
.btn{position:absolute;display:flex;align-items:center;justify-content:center;background:var(--red);color:var(--white);font-weight:600;border-radius:6px;text-decoration:none;letter-spacing:.5px}
.photo{position:absolute}

/* hero */
.hero{position:absolute;left:0;top:0;width:1200px;height:604px;background:linear-gradient(100deg,#eef2f8 0%,#d6e1ef 35%,#9fb3c8 60%,#5d6e5b 82%,#3c4a35 100%)}
.hero-truck{position:absolute;left:640px;top:90px;width:520px;height:380px;background:linear-gradient(160deg,#f4f4f4,#cfd3d6 70%,#6c7378);border-radius:8px;opacity:.85}
.hero-ground{position:absolute;left:0;top:430px;width:1200px;height:174px;background:linear-gradient(180deg,rgba(190,180,160,.0),rgba(150,140,120,.6))}
.logo{position:absolute;left:48px;top:22px;display:flex;align-items:center;gap:12px}
.logo .mark{width:52px;height:52px;border-radius:50%;background:var(--navy)}
.logo span{font-family:"Poppins",sans-serif;font-weight:600;font-size:30px;color:var(--navy)}
.nav{position:absolute;left:469px;top:28px;display:flex;gap:0;align-items:center}
.nav a{display:block;color:var(--white);font-size:15px;font-weight:600;text-decoration:none;padding:7px 12px;letter-spacing:.3px;margin-right:12px}
.nav a.active{background:var(--red)}
.portal{position:absolute;left:1009px;top:24px;width:168px;height:37px;border:2px solid var(--white);border-radius:8px;color:var(--white);font-family:"Poppins",sans-serif;font-weight:600;font-size:14px;display:flex;align-items:center;justify-content:center;letter-spacing:.3px}
.hero h1{position:absolute;left:120px;top:226px;font-size:40px;line-height:56px;color:var(--navy);font-weight:700}
.dots{position:absolute;left:563px;top:558px;display:flex;gap:10px;align-items:center}
.dots i{display:block;width:6px;height:6px;border-radius:50%;background:var(--white)}
.dots i.on{width:12px;height:12px;border:3px solid var(--white);background:var(--red)}

/* welcome */
.welcome{position:absolute;left:0;top:604px;width:1200px;height:495px;background:var(--blue);color:var(--white)}
.welcome .kicker{position:absolute;left:132px;top:60px;font-family:"Poppins",sans-serif;font-weight:600;font-size:19px}
.welcome h2{position:absolute;left:132px;top:82px;font-size:33px;font-weight:600}
.welcome h2 b{font-size:52px;font-weight:600}
.welcome .rule{position:absolute;left:134px;top:150px;width:70px;height:3px;background:var(--white)}
.welcome p{position:absolute;left:132px;top:188px;width:340px;font-size:15px;line-height:22.5px}

/* road band */
.band{position:absolute;left:0;top:1099px;width:1200px;height:370px;background:linear-gradient(180deg,#3d4a36 0%,#5e6a55 35%,#7a7f79 60%,#3b4238 100%)}
.card{position:absolute;left:132px;top:1273px;width:938px;height:557px;background:var(--white);box-shadow:0 4px 14px rgba(0,0,0,.12)}
.card h2{position:absolute;left:0;top:34px;width:100%;text-align:center;font-size:26px;font-weight:600}
.card .lead{position:absolute;left:140px;top:94px;width:658px;text-align:center;font-size:13px;line-height:20px}
.svc{position:absolute;top:200px;width:236px;height:240px;text-align:center}
.svc svg{display:block;margin:0 auto}
.svc h3{font-size:15px;font-weight:600;margin-top:30px}
.svc p{font-size:12.5px;line-height:18px;color:var(--muted);width:180px;margin:10px auto 0}
.divider{position:absolute;top:190px;width:1px;height:245px;background:#dedede}

/* specialize */
.title{position:absolute;left:0;width:1200px;text-align:center;font-size:26px;font-weight:600}
.sub{position:absolute;left:0;width:1200px;text-align:center;font-size:13px}
.spec-icon{position:absolute;width:76px;height:76px;border-radius:22px;background:var(--blue);display:flex;align-items:center;justify-content:center}
.spec-text{position:absolute;font-size:12.5px;line-height:18px;color:var(--muted)}
.spec-text h4{font-size:15px;font-weight:600;color:var(--ink);margin-bottom:8px}
.globe{position:absolute;left:409px;top:2166px;width:382px;height:295px;overflow:hidden;border-radius:191px 191px 0 0;background:linear-gradient(180deg,#d9c4a2 0%,#e9e5de 35%,#b7b9b8 65%,#6f776d 100%)}

/* what we do */
.what{position:absolute;left:0;top:2461px;width:1200px;height:762px;background:var(--white)}
.tile{position:absolute;width:300px;height:220px}
.tile-label{position:absolute;width:300px;text-align:center;font-family:"Poppins",sans-serif;font-weight:600;font-size:17px}

/* blog */
.blog{position:absolute;left:0;top:3223px;width:1200px;height:552px;background:var(--blue);color:var(--white)}
.blog h2{position:absolute;left:0;width:1200px;top:46px;text-align:center;font-size:25px;font-weight:500}
.blog .rule{position:absolute;left:578px;top:100px;width:50px;height:3px;background:var(--white)}
.post{position:absolute;top:160px;width:294px;height:313px;border:2px solid var(--white)}
.post h3{position:absolute;left:26px;top:30px;width:250px;font-size:17.5px;line-height:27px;font-weight:500}
.post p{position:absolute;left:30px;top:146px;width:220px;font-size:12.5px;line-height:17.6px;opacity:.9}
.post .btn{left:30px;top:293px;width:98px;height:33px;font-size:12px;border-radius:5px}

/* help */
.help{position:absolute;left:0;top:3775px;width:1200px;height:356px;background:var(--teal);color:var(--white);text-align:center}
.help h2{position:absolute;left:0;width:1200px;top:62px;font-size:32px;font-weight:800}
.help p{position:absolute;left:280px;top:140px;width:640px;font-size:18px;line-height:29px}

/* footer */
.footer{position:absolute;left:0;top:4131px;width:1200px;height:340px;background:var(--footer);color:var(--white)}
.f-logo{position:absolute;left:139px;top:102px;display:flex;align-items:center;gap:18px}
.f-logo .mark{width:68px;height:68px;border-radius:50%;background:var(--blue)}
.f-logo span{font-family:"Poppins",sans-serif;font-weight:600;font-size:25px}
.f-col h4{font-size:13px;font-weight:600;letter-spacing:.5px;margin-bottom:20px}
.f-col{position:absolute;top:52px;font-size:11.5px}
.f-menu a{display:block;color:var(--white);text-decoration:none;line-height:20px}
.f-item{display:flex;align-items:center;gap:14px;margin-bottom:18px;line-height:16px}
.f-item .ic{width:24px;height:24px;border-radius:50%;background:var(--white);display:flex;align-items:center;justify-content:center;flex:none}
.f-rule{position:absolute;left:139px;top:261px;width:922px;height:1px;background:#444}
.copy{position:absolute;left:0;width:1200px;top:304px;text-align:center;font-size:10px;color:#cfcfcf}
</style>
</head>
<body>

<!-- hero -->
<header class="hero">
  <div class="photo" role="img" aria-label="White semi truck driving on a mountain road at dusk" style="inset:0">
    <div class="hero-ground"></div>
    <div class="hero-truck"></div>
  </div>
  <div class="logo"><div class="mark"></div><span>Caldera Logistics</span></div>
  <nav class="nav">
    <a class="active" href="#">HOME</a>
    <a href="#">ABOUT US</a>
    <a href="#">SERVICES</a>
    <a href="#">CAREERS</a>
    <a href="#">CONTACT US</a>
  </nav>
  <a class="portal" href="#">CUSTOMER PORTAL</a>
  <h1>Accurately Promising,<br>Reliably Delivering</h1>
  <a class="btn" href="#" style="left:120px;top:365px;width:151px;height:48px;font-size:15px">GET STARTED</a>
  <div class="dots"><i></i><i></i><i class="on"></i><i></i><i></i></div>
</header>

<!-- welcome -->
<section class="welcome">
  <div class="kicker">Welcome to</div>
  <h2><b>C</b>aldera Logistics</h2>
  <div class="rule"></div>
  <p>There are many variations of passages of Lorem Ipsum available, but the majority have suffered alteration in some form, by injected humour, or randomised words which don't look even slightly believable. If you are going to use a passage of Lorem Ipsum, you need to be sure there isn't anything embarrassing hidden in the middle of text.</p>
  <a class="btn" href="#" style="left:134px;top:396px;width:107px;height:35px;font-size:13px">READ MORE</a>
  <div class="photo" role="img" aria-label="Semi truck on a highway at sunset" style="left:535px;top:58px;width:535px;height:382px;background:linear-gradient(180deg,#3a4f7a 0%,#6b7da0 40%,#d49a5a 62%,#2a2f3a 80%,#1a1d24 100%)"></div>
</section>

<!-- services -->
<div class="band" role="img" aria-label="Aerial view of trucks on a highway through green hills"></div>
<section class="card">
  <h2>Global Integrated Logistics</h2>
  <p class="lead">Caldera Logistics specializes in moving regulated and non-regulated chemical freight of all kinds Operating in 49 states and Canada Caldera Logistics' focus is in brokering van or flatbed, tanker endorsed, liquid bulk, drayage, intermodal, and international chemical shipments of all combinations.</p>

  <div class="svc" style="left:0">
    <svg width="112" height="60" viewBox="0 0 112 60" fill="none" stroke="#2b5ea7" stroke-width="2.5"><rect x="4" y="4" width="72" height="40" rx="2"/><path d="M76 16h18l12 14v14H76z"/><path d="M82 20h10l7 9H82z"/><line x1="2" y1="48" x2="108" y2="48"/><circle cx="20" cy="52" r="5"/><circle cx="34" cy="52" r="5"/><circle cx="92" cy="52" r="5"/></svg>
    <h3>Expedited freight</h3>
    <p>Meeting deadlines is everything to the recipient of the shipment. With teams and dedicated carriers Caldera logistics happen.</p>
  </div>
  <div class="divider" style="left:233px"></div>
  <div class="svc" style="left:234px">
    <svg width="60" height="68" viewBox="0 0 60 68" fill="none" stroke="#2b5ea7" stroke-width="2.5"><path d="M6 4h34l12 12v48H6z"/><path d="M40 4v12h12"/><line x1="14" y1="26" x2="40" y2="26"/><line x1="14" y1="34" x2="40" y2="34"/><line x1="14" y1="42" x2="32" y2="42"/><line x1="14" y1="50" x2="28" y2="50"/><path d="M56 30L36 54l-4 6 6-3 20-24z"/></svg>
    <h3>Contract Logistics</h3>
    <p>With a network of carriers and contracted lanes of freight. Caldera logistics is capable of staying below market rates.</p>
  </div>
  <div class="divider" style="left:468px"></div>
  <div class="svc" style="left:469px">
    <svg width="64" height="68" viewBox="0 0 64 68" fill="none" stroke="#2b5ea7" stroke-width="2.5"><path d="M10 64c4-14 20-14 20-28S46 20 50 4"/><path d="M26 64c4-12 18-12 18-26S58 20 62 6"/><path d="M18 64l2-4M28 48l3-4M38 30l3-4M49 14l2-4" stroke-dasharray="3 4"/><circle cx="14" cy="26" r="5"/><path d="M14 31v10"/></svg>
    <h3>Road Freight</h3>
    <p>There are many variations of passages of Lorem Ipsum available, but the majority have suffered alter.</p>
  </div>
  <div class="divider" style="left:703px"></div>
  <div class="svc" style="left:703px">
    <svg width="96" height="90" viewBox="0 0 96 90" fill="none" stroke="#2b5ea7" stroke-width="2.5"><path d="M34 14l14-8 14 8v16l-14 8-14-8z"/><path d="M34 14l14 8 14-8M48 22v16"/><line x1="48" y1="2" x2="48" y2="6"/><rect x="30" y="42" width="36" height="22"/><path d="M66 50h12l8 10v8H66"/><path d="M6 70h82"/><circle cx="40" cy="76" r="6"/><circle cx="76" cy="76" r="6"/><path d="M4 54l22 4"/></svg>
    <h3>Intermodal</h3>
    <p>There are many variations of passages of Lorem Ipsum available, but the majority have suffered alter.</p>
  </div>

  <a class="btn" href="#" style="left:385px;top:481px;width:164px;height:34px;font-size:13px">VIEW ALL SERVICES</a>
</section>

<!-- specialize -->
<h2 class="title" style="top:1900px">We Specialize In</h2>
<p class="sub" style="top:1959px">There are many variations of passages of Lorem Ipsum available lorem ipsum</p>

<svg class="abs" style="left:270px;top:2080px" width="660" height="160" viewBox="0 0 660 160" fill="none" stroke="#dcd6d6" stroke-width="1"><line x1="0" y1="0" x2="150" y2="136"/><line x1="650" y1="0" x2="510" y2="136"/></svg>

<div class="spec-icon" style="left:483px;top:2053px">
  <svg width="44" height="44" viewBox="0 0 44 44" fill="none" stroke="#fff" stroke-width="2.5"><path d="M6 28a14 12 0 0 0 28 0z"/><path d="M20 28l16-18"/><circle cx="38" cy="8" r="3"/><circle cx="13" cy="33" r="1.5" fill="#fff"/><circle cx="21" cy="35" r="1.5" fill="#fff"/></svg>
</div>
<div class="spec-text" style="left:580px;top:2054px;width:170px"><h4>Chemicals</h4>Corrosive 8 and Flammable 3 class chemicals</div>

<div class="globe" role="img" aria-label="White semi truck on a highway, framed in a half circle"></div>

<div class="spec-icon" style="left:134px;top:2249px">
  <svg width="48" height="40" viewBox="0 0 48 40" fill="none" stroke="#fff" stroke-width="2.5"><path d="M4 24h40l-6 10H10z"/><rect x="12" y="14" width="8" height="10"/><rect x="22" y="14" width="8" height="10"/><rect x="32" y="10" width="6" height="14"/><path d="M2 38c4 0 4-2 8-2s4 2 8 2 4-2 8-2 4 2 8 2 4-2 8-2"/></svg>
</div>
<div class="spec-text" style="left:227px;top:2243px;width:170px"><h4>Drayage</h4>Whether Sea or Rail Port Caldera Logistics has relationships that prove to avoid demurrage and move your freight to it's final destination.</div>

<div class="spec-icon" style="left:815px;top:2249px">
  <svg width="48" height="40" viewBox="0 0 48 40" fill="none" stroke="#fff" stroke-width="2.5"><rect x="4" y="6" width="40" height="28"/><path d="M12 6v28M18 6v28M24 6v28M30 6v28M36 6v28"/></svg>
</div>
<div class="spec-text" style="left:912px;top:2246px;width:150px"><h4>LTL</h4>Having negotiated rates with over 120 LTL carriers give any shipper their choice in moving their cargo.</div>

<!-- what we do -->
<section class="what">
  <h2 class="title" style="top:49px">What We Do</h2>
  <p class="sub" style="top:96px">There are many variations of passages of Lorem Ipsum available lorem ipsum</p>

  <div class="tile" role="img" aria-label="Storm drain grate in gravel" style="left:132px;top:151px;background:linear-gradient(135deg,#8a5a40,#6e6d66 45%,#8f9588)"></div>
  <div class="tile-label" style="left:132px;top:388px">Drayage</div>
  <div class="tile" role="img" aria-label="White van on a desert road below a mountain" style="left:450px;top:151px;background:linear-gradient(180deg,#9ec3e4 0%,#c9b3a5 40%,#eef0f1 60%,#b0966d 100%)"></div>
  <div class="tile-label" style="left:450px;top:388px">Dry Van</div>
  <div class="tile" role="img" aria-label="Car wheel on a flatbed trailer" style="left:769px;top:151px;background:linear-gradient(135deg,#b7bcc2,#6a6d72 50%,#c3c6c9)"></div>
  <div class="tile-label" style="left:769px;top:388px">Flatbed</div>

  <div class="tile" role="img" aria-label="Tanker truck beside a river in green hills" style="left:132px;top:441px;background:linear-gradient(180deg,#c9d6e6 0%,#6c8f58 45%,#cfd2d3 70%,#5d7a4c 100%)"></div>
  <div class="tile-label" style="left:132px;top:678px">Liquid Bulk</div>
  <div class="tile" role="img" aria-label="Refrigerated trailer unit" style="left:450px;top:441px;background:linear-gradient(180deg,#e9ecee,#c6cbd0 60%,#5f6670)"></div>
  <div class="tile-label" style="left:450px;top:678px">Reefer</div>
  <div class="tile" role="img" aria-label="Box truck on a dark road at dusk" style="left:769px;top:441px;background:linear-gradient(135deg,#2a2a30,#5b4a40 45%,#8a2a2a 65%,#2a2a30)"></div>
  <div class="tile-label" style="left:769px;top:678px">Hot Shot/Box Trucks</div>
</section>

<!-- blog -->
<section class="blog">
  <h2>Latest Blog</h2>
  <div class="rule"></div>
  <article class="post" style="left:139px">
    <h3>Lorem Ipsum is simply dummy text of the printing and typesetting industry</h3>
    <p>Sed ut perspiciatis unde omnis iste natus error sit voluptatem accusantium doloremque laudantium, totam rem aperiam, eaque ipsa quae ab illo inventore veritatis et quasi architecto beatae vitae dicta s</p>
    <a class="btn" href="#">READ MORE</a>
  </article>
  <article class="post" style="left:460px">
    <h3>Lorem Ipsum is simply dummy text of the printing and typesetting industry</h3>
    <p>Sed ut perspiciatis unde omnis iste natus error sit voluptatem accusantium doloremque laudantium, totam rem aperiam, eaque ipsa quae ab illo inventore veritatis et quasi architecto beatae vitae dicta s</p>
    <a class="btn" href="#">READ MORE</a>
  </article>
  <article class="post" style="left:781px">
    <h3>Lorem Ipsum is simply dummy text of the printing and typesetting industry</h3>
    <p>Sed ut perspiciatis unde omnis iste natus error sit voluptatem accusantium doloremque laudantium, totam rem aperiam, eaque ipsa quae ab illo inventore veritatis et quasi architecto beatae vitae dicta s</p>
    <a class="btn" href="#">READ MORE</a>
  </article>
</section>

<!-- help -->
<section class="help">
  <h2>HOW CAN WE HELP YOU?</h2>
  <p>At vero eos et accusamus et iusto odio dignissimos ducimus qui blanditiis praesentium voluptatum deleniti atque corrupti quos dolores et quas molestias excepturi sint occaecati cupiditate non provident,</p>
  <a class="btn" href="#" style="left:519px;top:257px;width:139px;height:42px;font-size:13px">CONTACT US</a>
</section>

<!-- footer -->
<footer class="footer">
  <div class="f-logo"><div class="mark"></div><span>Harborline Freight</span></div>

  <div class="f-col f-menu" style="left:486px">
    <h4>MENU</h4>
    <a href="#">HOME</a><a href="#">ABOUT US</a><a href="#">SERVICES</a><a href="#">CAREERS</a><a href="#">CONTACT US</a>
  </div>

  <div class="f-col" style="left:677px">
    <h4>CONTACT US</h4>
    <div class="f-item"><span class="ic"><svg width="12" height="14" viewBox="0 0 12 14"><path d="M6 0a5 5 0 0 0-5 5c0 4 5 9 5 9s5-5 5-9a5 5 0 0 0-5-5zm0 7a2 2 0 1 1 0-4 2 2 0 0 1 0 4z" fill="#232323"/></svg></span><span>5702 Marlow Ridge Road<br>Fenwick, CA 90418</span></div>
    <div class="f-item"><span class="ic"><svg width="12" height="12" viewBox="0 0 12 12"><path d="M2 0l3 3-1.5 2A8 8 0 0 0 7 8.5L9 7l3 3-2 2C5 12 0 7 0 2z" fill="#232323"/></svg></span><span>Call Us<br>555.014.2290</span></div>
    <div class="f-item"><span class="ic"><svg width="12" height="10" viewBox="0 0 12 10" fill="none" stroke="#232323" stroke-width="1.5"><rect x="1" y="1" width="10" height="8"/><path d="M1 1l5 4 5-4"/></svg></span><span>E mail Us<br>info@harborlinefreight.com</span></div>
  </div>

  <div class="f-col" style="left:967px">
    <h4>FOLLOW US</h4>
    <div class="f-item"><span class="ic"></span><span>Like us on<br>FRIENDWALL</span></div>
    <div class="f-item"><span class="ic"></span><span>Follow us on<br>CHIRPER</span></div>
    <div class="f-item"><span class="ic"></span><span>Follow us on<br>WORKLINE</span></div>
  </div>

  <div class="f-rule"></div>
  <p class="copy">Copyright © 2021 All Rights Reserved</p>
</footer>

</body>
</html>
```